Marlow Sail Works President Business Card Carbon fiber catamarans

Hi.. I need a new business card design.. I am the President of a high tech yacht builder. We build Carbon Fiber go fast catamarans... Maybe we use the file I am sharing to you as the back of the card.. We need to look cool and crisp ...

Target Market(s)

Affluent People who will purchase a cool yacht

Industry/Entity Type

Custom Yacht Builder

Contact Information for Business Card

Dean Pellway , President, 731.508.2164 USA

Font styles to use
Serif

Requirements
Must have
• the clean crisp cool feel
Nice to have
• clean and crisp
Should not have
• Bold ugly

```html
<!DOCTYPE html>
<html lang="en">
<head>
<meta charset="utf-8">
<title>Marlow Sail Works – Business Card</title>
<link href="https://fonts.googleapis.com/css2?family=Michroma&family=Nunito+Sans:wght@400&display=swap" rel="stylesheet">
<style>
  :root {
    --backdrop: #1e1e1e;
    --card: #0c0c0c;
    --silver: #d9d9d9;
    --silver-soft: #bdbdbd;
    --rule: #3a3a3a;
  }
  * { box-sizing: border-box; margin: 0; padding: 0; }
  html, body { width: 1200px; height: 900px; overflow: hidden; }
  body {
    background: var(--backdrop);
    display: flex;
    flex-direction: column;
    align-items: center;
    justify-content: center;
    gap: 36px;
    font-family: "Nunito Sans", sans-serif;
  }
  .card {
    position: relative;
    width: 700px;
    height: 400px;
    background: var(--card);
    box-shadow: 0 14px 30px rgba(0,0,0,0.55);
  }
  .wordmark {
    font-family: "Michroma", sans-serif;
    color: var(--silver);
    text-transform: uppercase;
    display: flex;
    align-items: center;
    gap: 16px;
  }
  .wordmark-dot {
    border-radius: 50%;
    border: 2px solid var(--silver);
    flex: none;
  }
  .wordmark-name { line-height: 1.25; letter-spacing: 0.12em; }

  /* Front */
  .card-front .wordmark {
    position: absolute;
    left: 48px;
    top: 250px;
  }
  .card-front .wordmark-dot { width: 44px; height: 44px; }
  .card-front .wordmark-name { font-size: 18px; }
  .divider {
    position: absolute;
    left: 388px;
    top: 70px;
    width: 1px;
    height: 230px;
    background: var(--rule);
  }
  .contact {
    position: absolute;
    left: 418px;
    top: 78px;
    color: var(--silver);
  }
  .contact-name {
    font-family: "Michroma", sans-serif;
    font-size: 17px;
    letter-spacing: 0.14em;
    text-transform: uppercase;
  }
  .contact-title { font-size: 15px; color: var(--silver-soft); margin-top: 2px; }
  .contact-list { list-style: none; margin-top: 26px; }
  .contact-list li {
    display: flex;
    align-items: center;
    gap: 10px;
    font-size: 15px;
    line-height: 26px;
  }
  .contact-list li.address { margin-top: 22px; }
  .contact-list svg { width: 15px; height: 15px; flex: none; }

  /* Back */
  .card-back {
    display: flex;
    align-items: center;
    justify-content: center;
  }
  .card-back .wordmark-dot { width: 70px; height: 70px; border-width: 3px; }
  .card-back .wordmark-name { font-size: 30px; }
</style>
</head>
<body>

  <section class="card card-front">
    <div class="wordmark">
      <span class="wordmark-dot"></span>
      <span class="wordmark-name">Marlow<br>Sail Works</span>
    </div>
    <div class="divider"></div>
    <div class="contact">
      <p class="contact-name">Dean Pellway</p>
      <p class="contact-title">President</p>
      <ul class="contact-list">
        <li>
          <svg viewBox="0 0 16 16" aria-hidden="true"><path d="M4 1.5l2.2 2.6-1.3 1.6c.8 1.8 2.3 3.3 4.1 4.1l1.6-1.3 2.6 2.2-1.4 2.2C6.5 12.6 3.3 9.4 1.9 3.7z" fill="none" stroke="var(--silver)" stroke-width="1.3"/></svg>
          731.508.2164
        </li>
        <li>
          <svg viewBox="0 0 16 16" aria-hidden="true"><rect x="1.5" y="3.5" width="13" height="9" fill="none" stroke="var(--silver)" stroke-width="1.3"/><path d="M1.5 3.5L8 9l6.5-5.5" fill="none" stroke="var(--silver)" stroke-width="1.3"/></svg>
          info@marlowsail.com
        </li>
        <li>
          <svg viewBox="0 0 16 16" aria-hidden="true"><circle cx="8" cy="8" r="6.5" fill="none" stroke="var(--silver)" stroke-width="1.2"/><ellipse cx="8" cy="8" rx="2.8" ry="6.5" fill="none" stroke="var(--silver)" stroke-width="1.1"/><path d="M1.5 8h13M2.6 4.7h10.8M2.6 11.3h10.8" stroke="var(--silver)" stroke-width="1"/></svg>
          www.marlowsailworks.com
        </li>
        <li class="address">
          <svg viewBox="0 0 16 16" aria-hidden="true"><path d="M8 15s5-5.2 5-9A5 5 0 0 0 3 6c0 3.8 5 9 5 9z" fill="var(--silver)"/><circle cx="8" cy="6" r="1.8" fill="var(--card)"/></svg>
          North Harbor 40512, USA
        </li>
      </ul>
    </div>
  </section>

  <section class="card card-back">
    <div class="wordmark">
      <span class="wordmark-dot"></span>
      <span class="wordmark-name">Marlow<br>Sail Works</span>
    </div>
  </section>

</body>
</html>
```